Corvel Capital LLC

Need Professional Business cards for New Investment Fund

Target Market(s)

High Quality investors

Industry/Entity Type

Financial

Contact Information for Business Card

Phone Number +1 555 284 6190
Name Lukas Varenko
Title Fund Manager
email lv@FundCorvel.com
Website www.FundCorvel.com

Colors

Designer to choose colors to be used in the design.

Requirements
Must have
• Must have our Logo and all of the above. Must be made so lettering and loge can be raised

```html
<!DOCTYPE html>
<html lang="en">
<head>
<meta charset="UTF-8">
<title>Lirvane — Business Card</title>
<link href="https://fonts.googleapis.com/css2?family=Montserrat:wght@500;600&display=swap" rel="stylesheet">
<style>
  :root {
    --backdrop: #3a3a3a;
    --card: #262626;
    --accent: #5cbf45;
    --text-light: #f2f2f2;
    --text-muted: #d8d8d8;
  }
  * { box-sizing: border-box; margin: 0; padding: 0; }
  html, body {
    width: 1200px;
    height: 900px;
    overflow: hidden;
  }
  body {
    background: var(--backdrop);
    font-family: "Montserrat", Arial, sans-serif;
    position: relative;
  }
  .card {
    position: absolute;
    left: 290px;
    width: 620px;
    height: 354px;
    background: var(--card);
    box-shadow: 0 12px 30px rgba(0,0,0,0.45);
  }
  .card--front { top: 80px; }
  .card--back { top: 466px; }

  .brand {
    display: flex;
    align-items: center;
    gap: 12px;
    color: var(--accent);
    font-weight: 600;
    letter-spacing: 0.08em;
    text-transform: uppercase;
    white-space: nowrap;
  }
  .brand__mark {
    width: 18px;
    height: 18px;
    background: var(--accent);
    flex: none;
  }
  .card--front .brand {
    position: absolute;
    inset: 0;
    justify-content: center;
    font-size: 40px;
  }
  .card--back .brand {
    position: absolute;
    left: 38px;
    top: 0;
    height: 100%;
    font-size: 28px;
  }
  .divider {
    position: absolute;
    left: 258px;
    top: 46px;
    width: 2px;
    height: 262px;
    background: var(--accent);
  }
  .contact {
    position: absolute;
    left: 298px;
    top: 84px;
  }
  .contact__name {
    color: var(--text-light);
    font-size: 22px;
    font-weight: 600;
    letter-spacing: 0.03em;
  }
  .contact__title {
    color: var(--text-muted);
    font-size: 16px;
    font-weight: 500;
    margin-bottom: 20px;
  }
  .contact__list { list-style: none; }
  .contact__item {
    display: flex;
    align-items: center;
    gap: 12px;
    color: var(--text-light);
    font-size: 19px;
    font-weight: 500;
    margin-bottom: 12px;
  }
  .contact__icon {
    width: 20px;
    height: 20px;
    fill: var(--accent);
    flex: none;
  }
</style>
</head>
<body>
  <section class="card card--front">
    <div class="brand"><span class="brand__mark"></span>Lirvane</div>
  </section>

  <section class="card card--back">
    <div class="brand"><span class="brand__mark"></span>Lirvane</div>
    <div class="divider"></div>
    <div class="contact">
      <p class="contact__name">Lukas Varenko</p>
      <p class="contact__title">Fund Manager</p>
      <ul class="contact__list">
        <li class="contact__item">
          <svg class="contact__icon" viewBox="0 0 24 24" aria-hidden="true"><path d="M6.6 10.8a15.1 15.1 0 0 0 6.6 6.6l2.2-2.2a1 1 0 0 1 1-.25 11.4 11.4 0 0 0 3.6.57 1 1 0 0 1 1 1V20a1 1 0 0 1-1 1A17 17 0 0 1 3 4a1 1 0 0 1 1-1h3.5a1 1 0 0 1 1 1c0 1.25.2 2.45.57 3.57a1 1 0 0 1-.25 1z"/></svg>
          +1 555 284 6190
        </li>
        <li class="contact__item">
          <svg class="contact__icon" viewBox="0 0 24 24" aria-hidden="true"><path d="M2 5h20v14H2z"/><path d="M2 5h20L12 12.5z" fill="#1c1c1c" opacity="0.35"/></svg>
          lv@FundCorvel.com
        </li>
        <li class="contact__item">
          <svg class="contact__icon" viewBox="0 0 24 24" aria-hidden="true"><circle cx="12" cy="12" r="10"/><path d="M2 12h20M12 2c3 3 3 17 0 20M12 2c-3 3-3 17 0 20" stroke="#262626" stroke-width="1.4" fill="none"/></svg>
          www.FundCorvel.com
        </li>
      </ul>
    </div>
  </section>
</body>
</html>
```